Duct Manufacturing Company new to the industry needs business card and stationary design

we are sheet metal duct manufacturers looking for a business card design to fit my new business logo.
nothing to crazy that will date, but want it to stand out from the crowed.
I'm sure you guys will work it out.

Contact Information for Business Card

Glen Marsh
Director

Address
17 Dorwell St
Karrowdale NSW 2695

0438 760 514

Sales@flowbend.com.au

Font styles to use
Other font styles liked:
• BankGothic md bt

Requirements
Nice to have
• Like the idea of corner rounded to match logo
• like to keep colours flowing
• font I like sharp square not rounded

```html
<!DOCTYPE html>
<html lang="en">
<head>
<meta charset="utf-8">
<title>Flowbend Industries – Business Card</title>
<link href="https://fonts.googleapis.com/css2?family=Michroma&family=Montserrat:wght@400;500&display=swap" rel="stylesheet">
<style>
  :root {
    --backdrop: #d9d9d9;
    --card: #ffffff;
    --green: #7dbb2c;
    --green-dark: #4da22a;
    --blue: #1a6fc0;
    --blue-dark: #0b4e98;
    --ink: #3c3c3c;
    --muted: #666666;
    --rule: #e4e4e4;
  }
  * { margin: 0; padding: 0; box-sizing: border-box; }
  html, body { width: 1200px; height: 1200px; overflow: hidden; }
  body {
    background: var(--backdrop);
    position: relative;
    font-family: "Montserrat", sans-serif;
  }
  .card {
    position: absolute;
    left: 190px;
    width: 820px;
    height: 500px;
    background: var(--card);
    border-radius: 30px;
    overflow: hidden;
    box-shadow: 0 6px 18px rgba(0,0,0,0.18);
  }
  .card--front { top: 70px; }
  .card--back { top: 630px; }
  .card__bands { position: absolute; inset: 0; width: 100%; height: 100%; }

  .brand {
    position: absolute;
    display: flex;
    align-items: center;
    gap: 18px;
  }
  .brand__mark {
    width: 34px; height: 34px;
    border-radius: 50%;
    background: var(--green);
    flex: none;
  }
  .brand__name {
    font-family: "Michroma", sans-serif;
    color: var(--ink);
    font-size: 30px;
    line-height: 1.3;
    letter-spacing: 2px;
  }
  .card--front .brand { left: 50%; top: 190px; transform: translateX(-50%); }
  .card--back .brand { left: 60px; top: 180px; }
  .card--back .brand__name { font-size: 25px; }

  .divider {
    position: absolute;
    left: 400px; top: 40px;
    width: 1px; height: 310px;
    background: var(--rule);
  }
  .contact {
    position: absolute;
    left: 440px; top: 80px;
    color: var(--ink);
  }
  .contact__name {
    font-family: "Michroma", sans-serif;
    font-weight: 400;
    color: var(--blue);
    font-size: 24px;
    letter-spacing: 2px;
  }
  .contact__role { font-size: 15px; color: var(--muted); margin: 6px 0 22px 20px; }
  .contact__list { list-style: none; font-size: 19px; line-height: 1.45; }
  .contact__list li { display: flex; gap: 12px; align-items: flex-start; }
  .contact__icon { width: 18px; height: 18px; margin-top: 4px; flex: none; }
  .contact__icon--none { visibility: hidden; }
  .website {
    position: absolute;
    right: 40px; bottom: 32px;
    color: #ffffff;
    font-size: 19px;
    letter-spacing: 0.5px;
  }
</style>
</head>
<body>

<section class="card card--front" aria-label="Card front">
  <svg class="card__bands" viewBox="0 0 820 500" preserveAspectRatio="none" aria-hidden="true">
    <polygon points="0,472 640,398 600,500 0,500" fill="var(--green)"/>
    <polygon points="0,488 620,430 600,500 0,500" fill="var(--green-dark)"/>
    <polygon points="640,398 820,362 820,500 600,500" fill="var(--blue)"/>
  </svg>
  <div class="brand">
    <span class="brand__mark"></span>
    <span class="brand__name">FLOWBEND<br>INDUSTRIES</span>
  </div>
</section>

<section class="card card--back" aria-label="Card back">
  <svg class="card__bands" viewBox="0 0 820 500" preserveAspectRatio="none" aria-hidden="true">
    <polygon points="0,450 520,400 500,500 0,500" fill="var(--green)"/>
    <polygon points="0,470 516,424 500,500 0,500" fill="var(--green-dark)" opacity="0.5"/>
    <polygon points="520,350 820,350 820,500 500,500" fill="var(--blue)"/>
    <polygon points="520,350 820,350 820,372 517,372" fill="var(--blue-dark)" opacity="0.4"/>
  </svg>

  <div class="brand">
    <span class="brand__mark"></span>
    <span class="brand__name">FLOWBEND<br>INDUSTRIES</span>
  </div>

  <div class="divider"></div>

  <div class="contact">
    <h1 class="contact__name">GLEN MARSH</h1>
    <p class="contact__role">Director</p>
    <ul class="contact__list">
      <li>
        <svg class="contact__icon" viewBox="0 0 18 18" aria-label="Phone"><path d="M3 6c0-2 2-3 6-3s6 1 6 3v1h-3V6H6v1H3z M4 9h10l1 6H3z" fill="var(--blue-dark)"/></svg>
        <span>0438 760 514</span>
      </li>
      <li>
        <svg class="contact__icon" viewBox="0 0 18 18" aria-label="Email"><rect x="1" y="4" width="16" height="11" fill="var(--blue-dark)"/><path d="M1 4l8 6 8-6" stroke="#fff" stroke-width="1.4" fill="none"/></svg>
        <span>Sales@flowbend.com.au</span>
      </li>
      <li>
        <svg class="contact__icon contact__icon--none" viewBox="0 0 18 18" aria-hidden="true"></svg>
        <span>17 Dorwell St<br>Karrowdale NSW 2695</span>
      </li>
    </ul>
  </div>

  <p class="website">www.flowbend.com.au</p>
</section>

</body>
</html>
```